The Visual Personality of Miss Cobbler Food Trailer

Something that stands out with color and our logo. This is a food trailer that attends several events in the spring and summer. We are known for being one of the best Gumbo producers in mid Michigan. We have been responsible for connecting different communities and cultures together and we are strong supporters of our veterans since this is a veteran owned business. All of our vegetables are fresh and locally purchased. These recipes are originally from New Orleans Louisiana. Our website is Misscobbler.net. This will be used for an 8" x 11" poster. Leave a box or area that states "WHERE WE WILL BE:" so that we can add the location of the event that we are attending.

Target Market(s)

We do cuisine that is recognized in the southern states of the USA. but live in the northern part of the USA. We are providing a menu of different southern recipes so they do not have to go all the way down south for get..

Industry/Entity Type

Food/Restaurant Industry

Font styles to use
Serif
Decorative

Colors
0094D4
00A9DD
6FCCEA
C7EBF8
E9F6FB
59FF00
82FF00
B8FF75
E3FFCB
F4FFEA
FFF300
FFF600
FEFA6F
FFFEC7
FFFEE8
EE7325
F08F49
F5BC92
FAE3D3
FDF4ED
EB3D1F
EC4F4E
F09395
F8D3D4
FCEDEE
A7469A
B969AE
D3A5CF
EDDBEB
F8F0F9

Requirements
Must have
• Our logo, which is "Miss Cobbler", "Homemade Deliciousness". We need an area on the poster where we can manually add the location of the event we will be attending because it changes weekly. location
Nice to have
• Bold colors and logo

```html
<!DOCTYPE html>
<html lang="en">
<head>
<meta charset="utf-8">
<title>Miss Cobbler Food Trailer Poster</title>
<link href="https://fonts.googleapis.com/css2?family=Fraunces:opsz,wght@9..144,600;9..144,700;9..144,800&family=Josefin+Sans:wght@600;700&family=Poppins:ital,wght@0,500;0,600;0,700;1,500;1,700&display=swap" rel="stylesheet">
<style>
  :root {
    --wine: #7d2a31;
    --ink: #3a3a3a;
    --paper: #f3f3f3;
    --stage: #e4e4e4;
    --cream: #efe4b4;
    --line: #5a5a5a;
    --box-line: #b9b9b9;
  }
  * { margin: 0; padding: 0; box-sizing: border-box; }
  html, body { width: 1200px; height: 1200px; overflow: hidden; }
  body { background: var(--stage); position: relative; font-family: "Fraunces", serif; }

  .poster {
    position: absolute; left: 150px; top: 15px; width: 900px; height: 1170px;
    background: linear-gradient(180deg, #f6f6f6 0%, #eeeeee 100%);
    overflow: hidden;
  }
  .abs { position: absolute; }

  /* brand block */
  .brand { left: 40px; top: 78px; width: 280px; text-align: center; }
  .brand-row { display: flex; align-items: center; justify-content: center; gap: 10px; white-space: nowrap; }
  .brand-dot { width: 24px; height: 24px; border-radius: 50%; background: var(--wine); flex: none; }
  .brand-name { font-family: "Fraunces", serif; font-weight: 700; font-size: 30px; color: var(--wine); line-height: 1; }
  .brand-tag { margin-top: 14px; font-family: "Poppins", sans-serif; font-weight: 700; font-size: 12px; color: var(--ink); letter-spacing: .5px; }

  .headline-main { left: 328px; top: 52px; width: 540px; font-family: "Josefin Sans", sans-serif; font-weight: 700; font-size: 83px; color: var(--wine); line-height: 1; white-space: nowrap; }
  .headline-sub { left: 330px; top: 150px; width: 540px; font-family: "Josefin Sans", sans-serif; font-weight: 600; font-size: 55px; color: var(--ink); line-height: 1; letter-spacing: 3px; white-space: nowrap; }

  /* food photos */
  .photo { right: 0; }
  .photo-pizza { top: 250px; width: 390px; height: 315px; border-radius: 60px 0 0 90px; background: radial-gradient(ellipse at 50% 50%, #d9a064 0%, #e6d7a0 60%, #ece3b9 100%); }
  .photo-gumbo { top: 540px; width: 370px; height: 355px; border-radius: 50% 0 0 50%; background: radial-gradient(circle at 55% 50%, #c96a3e 0%, #bf5a35 45%, #e7e3dc 78%); }
  .photo-poboy { top: 868px; width: 360px; height: 302px; border-radius: 90px 0 0 60px; background: linear-gradient(180deg, #c9854a 0%, #e8c9a2 45%, #d8775d 70%, #c48a56 100%); }

  .tag { width: 115px; height: 115px; border-radius: 50%; background: var(--cream); display: flex; flex-direction: column; align-items: center; justify-content: center; text-align: center; color: var(--ink); font-family: "Fraunces", serif; font-weight: 700; line-height: 1.05; opacity: .95; }
  .tag small { font-size: 15px; font-weight: 600; }
  .tag span { font-size: 24px; }
  .tag-pizza { left: 498px; top: 287px; }
  .tag-gumbo { left: 498px; top: 642px; }
  .tag-poboy { left: 498px; top: 1020px; }

  /* left copy */
  .copy { left: 55px; width: 370px; color: var(--ink); font-family: "Fraunces", serif; font-weight: 800; text-align: center; white-space: nowrap; }
  .copy-1 { top: 302px; font-size: 70px; line-height: 1; }
  .copy-2 { top: 370px; font-size: 70px; line-height: 1; }
  .copy-3 { top: 438px; font-size: 72px; line-height: 1; }
  .copy-3 .accent { color: var(--wine); }
  .ruled { display: flex; align-items: center; gap: 12px; }
  .ruled::before, .ruled::after { content: ""; flex: 1; height: 2px; background: var(--line); }
  .copy-and { top: 510px; font-size: 28px; font-weight: 700; }
  .copy-local { top: 538px; font-size: 38px; font-weight: 700; line-height: 1; }
  .divider { left: 55px; top: 597px; width: 370px; height: 2px; background: var(--wine); }
  .copy-recipes { top: 612px; font-size: 40px; font-weight: 700; line-height: 1; }
  .ribbon { left: 50px; top: 660px; width: 380px; height: 85px; }
  .ribbon-text { left: 50px; top: 668px; width: 380px; text-align: center; font-family: "Fraunces", serif; font-weight: 700; font-size: 54px; color: var(--wine); line-height: 1; }
  .copy-from { top: 744px; font-size: 32px; font-weight: 700; }
  .copy-place { top: 783px; font-size: 29px; font-weight: 700; color: var(--wine); }

  /* location box */
  .where { left: 55px; top: 846px; width: 370px; text-align: center; font-family: "Poppins", sans-serif; font-style: italic; font-weight: 700; font-size: 18px; color: var(--ink); }
  .where-box { left: 55px; top: 880px; width: 370px; height: 50px; border: 1.5px solid var(--box-line); border-radius: 6px; background: #f4f4f4; box-shadow: 0 10px 10px -8px rgba(0,0,0,.18); }

  /* contact */
  .info-label { left: 55px; top: 965px; width: 370px; text-align: center; font-family: "Poppins", sans-serif; font-style: italic; font-weight: 500; font-size: 14px; color: var(--ink); }
  .info-row { left: 40px; top: 988px; width: 400px; height: 46px; display: flex; align-items: center; justify-content: center; font-family: "Poppins", sans-serif; font-weight: 600; font-size: 15px; color: var(--ink); }
  .info-item { display: flex; align-items: center; gap: 8px; padding: 0 14px; white-space: nowrap; }
  .info-sep { width: 1.5px; height: 46px; background: var(--ink); }
  .icon-chip { width: 22px; height: 22px; border-radius: 3px; background: var(--wine); display: flex; align-items: center; justify-content: center; }
  .follow { left: 55px; top: 1055px; width: 370px; text-align: center; font-family: "Poppins", sans-serif; font-style: italic; font-weight: 500; font-size: 16px; color: var(--ink); }
  .socials { left: 55px; top: 1090px; width: 370px; display: flex; justify-content: center; gap: 30px; }
  .social-slot { width: 30px; height: 30px; border: 2.5px solid var(--wine); border-radius: 8px; }
  .handle { left: 55px; top: 1140px; width: 370px; text-align: center; font-family: "Poppins", sans-serif; font-weight: 700; font-size: 18px; color: var(--wine); }
</style>
</head>
<body>
<main class="poster">
  <div class="abs brand">
    <div class="brand-row"><span class="brand-dot"></span><span class="brand-name">Miss Cobbler</span></div>
    <div class="brand-tag">HOMEMADE DELICIOUSNESS!</div>
  </div>

  <h1 class="abs headline-main">HOMEMADE</h1>
  <h2 class="abs headline-sub">DELICIOUSNESS</h2>

  <div class="abs photo photo-pizza" role="img" aria-label="Langostino pizza topped with diced tomato and herbs"></div>
  <div class="abs photo photo-gumbo" role="img" aria-label="Bowl of chicken gumbo with peppers and tomato"></div>
  <div class="abs photo photo-poboy" role="img" aria-label="Shrimp po boy sandwich with lettuce, tomato and sauce"></div>

  <div class="abs tag tag-pizza"><small>Langostino</small><span>Pizza</span></div>
  <div class="abs tag tag-gumbo"><span>Chicken<br>Gumbo</span></div>
  <div class="abs tag tag-poboy"><span>Shrimp<br>Po Boy</span></div>

  <p class="abs copy copy-1">All of our</p>
  <p class="abs copy copy-2">vegetables</p>
  <p class="abs copy copy-3">are <span class="accent">Fresh</span></p>
  <p class="abs copy copy-and ruled">and</p>
  <p class="abs copy copy-local">locally purchased</p>
  <div class="abs divider"></div>
  <p class="abs copy copy-recipes">These recipes are</p>
  <svg class="abs ribbon" viewBox="0 0 380 85" aria-hidden="true">
    <path d="M22 4 H370 L356 42 L372 80 H10 L24 42 Z" fill="none" stroke="#7d2a31" stroke-width="3" stroke-linejoin="round"/>
  </svg>
  <p class="abs ribbon-text">Originally</p>
  <p class="abs copy copy-from ruled">from</p>
  <p class="abs copy copy-place">New Orleans Louisiana</p>

  <p class="abs where">WHERE WE WILL BE !</p>
  <div class="abs where-box"></div>

  <p class="abs info-label">Information:</p>
  <div class="abs info-row">
    <div class="info-item">Misscobbler.net
      <span class="icon-chip"><svg width="14" height="14" viewBox="0 0 14 14"><path d="M3 2 L11 7 L7 8 L9 12 L7.5 12.7 L5.6 8.8 L3 11 Z" fill="#fff"/></svg></span>
    </div>
    <span class="info-sep"></span>
    <div class="info-item">
      <span class="icon-chip"><svg width="14" height="14" viewBox="0 0 24 24"><path d="M6.6 10.8a15.1 15.1 0 0 0 6.6 6.6l2.2-2.2c.3-.3.7-.4 1-.2 1.1.4 2.3.6 3.6.6.6 0 1 .4 1 1V20c0 .6-.4 1-1 1A17 17 0 0 1 3 4c0-.6.4-1 1-1h3.5c.6 0 1 .4 1 1 0 1.3.2 2.5.6 3.6.1.3 0 .7-.2 1Z" fill="#fff"/></svg></span>
      555-0142-7788
    </div>
  </div>

  <p class="abs follow">Follow us on:</p>
  <div class="abs socials">
    <span class="social-slot"></span><span class="social-slot"></span><span class="social-slot"></span><span class="social-slot"></span>
  </div>
  <p class="abs handle">misscobbler</p>
</main>
</body>
</html>
```